Fabrication and machining company needing printed material designs.

Heron Vessels, Inc. wants to use appealing visuals as well as informative text to tell potential clients about our capabilities in fabrication and machining. We have a new logo to showcase as well as a new website. The use of print media will allow us to leave tangible information with clients, and therefore the design will need to be concise, informative, and visually appealing.

Full Page Flyer (approx. 8.5" x 11"), front and back design. This will be a detailed offering of capabilities and services for our shop.

Half Page Flyer (approx. 5.5" x 8.5"), front and back design. An abbreviated version of the full page flyer, meant to be easily handed out and stored inside a note book.

Bi-fold business card front and back. General offerings of our services. Minimal if any details. Finished size is twice the size of a business card (approx. 4" x 3.5"), once folded in half will be the same size as a standard business card (approx. 2" x 3.5").

Please use www.heronvesselsinc.example for theme ideas. The font used for our logo is ethnocentric, not to be used for all text.

Target Market(s)

Industrial Consumers

Font styles to use
Sans Serif

```html
<!DOCTYPE html>
<html lang="en">
<head>
<meta charset="utf-8">
<title>Heron Vessels, Inc. — Services &amp; Capabilities</title>
<link rel="stylesheet" href="https://fonts.googleapis.com/css2?family=Montserrat:wght@600;700;800&family=Open+Sans:wght@400;600&display=swap">
<style>
  :root {
    --orange: #f26a21;
    --ink: #1e1e1e;
    --text: #3a3a3a;
    --dark: #161616;
    --dark-2: #2a2a2a;
    --white: #ffffff;
  }
  * { margin: 0; padding: 0; box-sizing: border-box; }
  html, body { width: 849px; height: 1200px; overflow: hidden; background: var(--white); }
  .flyer {
    position: relative; width: 849px; height: 1200px; overflow: hidden;
    background: var(--white); font-family: "Open Sans", Arial, sans-serif; color: var(--text);
  }
  .backdrop { position: absolute; inset: 0; }
  .page-title {
    position: absolute; left: 50px; top: 24px;
    font-family: "Montserrat", Arial, sans-serif; font-weight: 800;
    font-size: 37px; color: var(--orange); letter-spacing: 0.2px;
  }
  .column { position: absolute; }
  .col-left { left: 50px; top: 78px; width: 240px; }
  .col-mid { left: 306px; top: 78px; width: 240px; }
  .col-right { left: 557px; top: 78px; width: 260px; }
  .service { margin-bottom: 16px; }
  .service h3 {
    font-family: "Montserrat", Arial, sans-serif; font-weight: 600;
    font-size: 22px; line-height: 1.1; color: var(--orange); margin-bottom: 4px;
  }
  .service ul { list-style: none; }
  .service li {
    position: relative; padding-left: 18px;
    font-size: 15px; line-height: 1.35; color: var(--text);
  }
  .service li::before {
    content: ""; position: absolute; left: 4px; top: 8px;
    width: 5px; height: 5px; border-radius: 50%; background: var(--ink);
  }
  .products { position: absolute; left: 410px; top: 668px; width: 420px; color: var(--white); }
  .products h2 {
    font-family: "Montserrat", Arial, sans-serif; font-weight: 800;
    font-size: 40px; color: var(--orange); margin-bottom: 8px;
  }
  .products ul { list-style: none; padding-left: 18px; }
  .products li {
    position: relative; padding-left: 20px;
    font-size: 17px; line-height: 1.75; color: var(--white);
  }
  .products li::before {
    content: "›"; position: absolute; left: 0; top: -1px;
    color: var(--orange); font-weight: 600; font-size: 20px;
  }
  .contact { position: absolute; left: 50px; top: 1070px; color: var(--white); }
  .contact .label {
    font-family: "Montserrat", Arial, sans-serif; font-weight: 800;
    font-size: 32px; line-height: 1.1; letter-spacing: 0.5px;
  }
  .contact .phone {
    font-family: "Montserrat", Arial, sans-serif; font-weight: 700;
    font-size: 32px; line-height: 1.1;
  }
  .website {
    position: absolute; right: 50px; top: 1103px;
    font-family: "Montserrat", Arial, sans-serif; font-weight: 700;
    font-size: 23px; color: var(--white);
  }
</style>
</head>
<body>
<main class="flyer">
  <svg class="backdrop" width="849" height="1200" viewBox="0 0 849 1200" aria-hidden="true">
    <defs>
      <linearGradient id="dark-fade" x1="0" y1="0" x2="1" y2="1">
        <stop offset="0" stop-color="#2a2a2a"/>
        <stop offset="1" stop-color="#111111"/>
      </linearGradient>
    </defs>
    <polygon points="849,300 849,1200 0,1200 0,1040 290,990 395,610" fill="url(#dark-fade)"/>
    <polyline points="849,300 395,610 290,990 0,1040" fill="none" stroke="var(--orange)" stroke-width="6"/>
    <polygon points="0,1045 290,996 260,1200 0,1200" fill="var(--dark)"/>
  </svg>

  <h1 class="page-title">OUR SERVICES &amp; CAPABILITIES</h1>

  <section class="column col-left">
    <div class="service"><h3>Design &amp; Engineering</h3>
      <ul><li>CAD Drawings</li><li>Engineering Services</li><li>3D Modelling</li></ul></div>
    <div class="service"><h3>Welding Processes</h3>
      <ul><li>Carbon Steel</li><li>Stainless Steel</li><li>Aluminium</li></ul></div>
    <div class="service"><h3>Paint and Corrosion Control</h3>
      <ul><li>Dedicated Paint Bay</li><li>Plural Component Application Equip</li><li>Multi Step liner Systems</li><li>Stainless Steel Passivation</li><li>Powder Coating</li><li>Galvanizing</li></ul></div>
    <div class="service"><h3>Sandblasting</h3>
      <ul><li>High Production Capacity</li></ul></div>
    <div class="service"><h3>Sandblasting</h3>
      <ul><li>High Production Capacity</li></ul></div>
    <div class="service"><h3>Hydraulic Assemblies</h3>
      <ul><li>System Testing</li><li>Hose Assemblies</li><li>Ram Rebuilding</li></ul></div>
  </section>

  <section class="column col-mid">
    <div class="service"><h3>Drivelines</h3>
      <ul><li>Custom Built</li><li>Rebuilding</li><li>Straightening</li></ul></div>
    <div class="service"><h3>Horizontal Lathes</h3>
      <ul><li>Upto 24" Dia &amp; 10' Long</li></ul></div>
    <div class="service"><h3>Vertical Lathes</h3>
      <ul><li>Upto 44" Dia</li></ul></div>
    <div class="service"><h3>Press Brake</h3>
      <ul><li>1" Plate x 5' Wide</li><li>3/8" Plate x14' Wide</li></ul></div>
    <div class="service"><h3>Iron Workers</h3>
      <ul><li>Upto 85 tons</li></ul></div>
    <div class="service"><h3>Band Saws</h3>
      <ul><li>22" Cut Capacity</li></ul></div>
  </section>

  <section class="column col-right">
    <div class="service"><h3>CNC Plasma Cutting</h3>
      <ul><li>Upto 44" Dia</li></ul></div>
    <div class="service"><h3>CNC Roll Forming</h3>
      <ul><li>1/2" x 10' Capacity</li></ul></div>
    <div class="service"><h3>Iron Workers</h3>
      <ul><li>Upto 85 tons</li></ul></div>
  </section>

  <section class="products">
    <h2>OUR PRODUCTS</h2>
    <ul>
      <li>Api 12-F, Api 650 Specification Built Tanks</li>
      <li>Fire Tubes/Tank Heaters</li>
      <li>Tank Coils</li>
      <li>Walkways</li>
      <li>Stairs</li>
      <li>Pump Skids</li>
    </ul>
  </section>

  <div class="contact">
    <p class="label">CALL US NOW</p>
    <p class="phone">(555) 310 - 4827</p>
  </div>
  <p class="website">www.heronvesselsinc.example</p>
</main>
</body>
</html>
```